Harbor Law Stationary - Law Firm

I am looking for a designer who can help me design letterhead and envelopes consistent with our new business cards. Feel free to reach out to me directly at ned@harborlawgroup.example. Thank you!! Visit harborlawgroup.example to see our site and the attached files for creative assets.

Target Market(s)

Anyone needing a lawyer

Font styles to use
Other font styles liked:
• Adobe Caslon Pro

Requirements
Must have
• Adobe Caslon Pro font
Full color
Nice to have
• My photo on front along with 2/3 face of camo - see mock up for example of what I have in mind.

American colors - similar to the ones found on my website and gold.

```html
<!DOCTYPE html>
<html lang="en">
<head>
<meta charset="utf-8">
<title>Harbor Law Stationery</title>
<link rel="stylesheet" href="https://fonts.googleapis.com/css2?family=Libre+Caslon+Text:wght@400&family=Montserrat:wght@300;400&display=swap">
<style>
:root{
  --gold:#ad9a5a;
  --navy:#0f2747;
  --ink:#333;
  --grey:#8a8a8a;
  --body:#7a7a7a;
  --rule:#555;
  --paper:#fff;
  --backdrop:#e8edf3;
}
*{margin:0;padding:0;box-sizing:border-box}
html,body{width:1200px;height:1200px;overflow:hidden;background:var(--backdrop)}
.canvas{position:relative;width:1200px;height:1200px}
.firm-name{font-family:Montserrat,Arial,sans-serif;font-weight:400;color:var(--navy);letter-spacing:1px;white-space:nowrap}

/* Letterhead */
.letterhead{position:absolute;left:77px;top:265px;width:460px;height:650px;background:var(--paper)}
.letterhead .firm-name{position:absolute;left:0;right:0;top:30px;text-align:center;font-size:15px}
.letterhead .head-rule{position:absolute;left:26px;right:26px;top:62px;border-top:1px solid var(--rule)}
.letter{position:absolute;left:47px;right:47px;top:0;font-family:Montserrat,Arial,sans-serif;color:var(--ink)}
.to-label{position:absolute;top:146px;left:0;font-size:8px;letter-spacing:1px}
.date{position:absolute;top:146px;right:0;font-size:6.5px;color:#555}
.recipient{position:absolute;top:161px;left:0}
.recipient .name{font-size:7.5px;color:var(--gold);margin-bottom:4px}
.recipient .line{font-size:5.5px;color:var(--grey);font-weight:300;line-height:10.3px}
.body{position:absolute;top:233px;left:0;right:0;font-size:6.3px;line-height:8.3px;font-weight:300;color:var(--body);text-align:justify}
.body p{margin-bottom:8.3px}
.signature{position:absolute;top:460px;left:0;width:80px;height:16px;background:#ececec}
.signer{position:absolute;top:488px;left:0;font-size:7.5px;color:var(--ink)}
.signer-title{position:absolute;top:498px;left:0;font-size:5.5px;color:var(--grey);font-weight:300}
.footer{position:absolute;left:0;right:0;top:613px;text-align:center;font-family:"Libre Caslon Text",Georgia,serif;font-weight:400;font-size:6.8px;color:var(--navy)}
.footer .addr{display:flex;align-items:center;justify-content:center;gap:4px}
.footer .addr::before,.footer .addr::after{content:"";width:26px;border-top:1px solid var(--navy)}
.footer .contacts{display:flex;align-items:center;justify-content:center;gap:5px;margin-top:3px}
.footer .contacts span{display:inline-flex;align-items:center;gap:2px}
.footer svg{width:6px;height:6px}
.gold-band{position:absolute;left:0;right:0;bottom:0;height:7px;background:var(--gold)}

/* Envelopes */
.envelope{position:absolute;left:574px;width:549px;height:239px;background:var(--paper)}
.envelope-front{top:311px}
.envelope-front .firm-name{position:absolute;left:48px;top:30px;font-size:15px}
.envelope-front .return-addr{position:absolute;left:48px;top:52px;font-family:"Libre Caslon Text",Georgia,serif;font-weight:400;font-size:7.4px;line-height:9.6px;color:var(--navy)}
.envelope-back{top:626px}
.flap{position:absolute;left:0;top:0;width:549px;height:66px}
.envelope-back .firm-name{position:absolute;left:0;right:0;top:25px;text-align:center;font-size:13px;color:var(--paper)}
</style>
</head>
<body>
<main class="canvas">

  <section class="letterhead">
    <div class="firm-name">Harbor Law</div>
    <div class="head-rule"></div>
    <div class="letter">
      <div class="to-label">TO</div>
      <div class="date">Friday, 01/01/2018</div>
      <div class="recipient">
        <div class="name">Dana Whitfield</div>
        <div class="line">Human Resources</div>
        <div class="line">Northwind Inc.</div>
        <div class="line">210-B Elm Court, Ridgeway</div>
        <div class="line">E89 USA</div>
      </div>
      <div class="body">
        <p>Thank you for your recent inquiry regarding our services. Our team has reviewed the documents you provided and prepared a short summary of the next steps. We will schedule a meeting with your department within two weeks to discuss the matter in detail, answer any open questions and agree on a clear timeline that suits both parties going forward.</p>
        <p>Please keep copies of all related records and correspondence. Bring them to our first meeting so we can review every detail together with care.</p>
        <p>We look forward to working with you.</p>
        <p>Our firm has represented clients across the region for many years. We believe that every case deserves careful attention, honest advice and steady support from the first call to the final outcome. Should anything change before our meeting, please contact our office and a member of our team will respond promptly.</p>
        <p>All information you share with us remains strictly confidential. We handle each file with the discretion it deserves and only share details with those directly involved in your matter. If you would like to add colleagues to our correspondence, simply let us know their names and roles, and we will update our records accordingly before the meeting takes place.</p>
        <p>Thank you again for your trust in our firm.</p>
      </div>
      <div class="signature" role="img" aria-label="Handwritten signature of Alan Mercer"></div>
      <div class="signer">Alan Mercer</div>
      <div class="signer-title">Managing Director</div>
    </div>
    <div class="footer">
      <div class="addr">48 Quayside Avenue Portview, Florida 32000</div>
      <div class="contacts">
        <span><svg viewBox="0 0 10 10" aria-hidden="true"><path d="M2 1l2 2-1 1.5c.6 1.2 1.4 2 2.5 2.5L7 6l2 2-1.5 1.5C4.5 9 1 5.5.5 2.5z" fill="var(--gold)"/></svg>555 010 2468</span>
        <span><svg viewBox="0 0 10 10" aria-hidden="true"><rect x=".5" y="2" width="9" height="6" fill="var(--gold)"/><path d="M.5 2l4.5 3.5L9.5 2" stroke="#fff" stroke-width=".8" fill="none"/></svg>ned@harborlawgroup.example</span>
        <span><svg viewBox="0 0 10 10" aria-hidden="true"><circle cx="5" cy="5" r="4.5" fill="var(--gold)"/><path d="M.5 5h9M5 .5c-2 2.5-2 6.5 0 9M5 .5c2 2.5 2 6.5 0 9" stroke="#fff" stroke-width=".6" fill="none"/></svg>harborlawgroup.example</span>
      </div>
    </div>
    <div class="gold-band"></div>
  </section>

  <section class="envelope envelope-front">
    <div class="firm-name">Harbor Law</div>
    <div class="return-addr">48 Quayside Avenue<br>Portview, Florida 32000</div>
    <div class="gold-band"></div>
  </section>

  <section class="envelope envelope-back">
    <svg class="flap" viewBox="0 0 549 66" aria-hidden="true"><path d="M0 0H549L537 40Q531 66 505 66H44Q18 66 12 40Z" fill="var(--navy)"/></svg>
    <div class="firm-name">Harbor Law</div>
  </section>

</main>
</body>
</html>
```